Federal IT Consulting Company - Brisolux Consulting Group

We're seeking a skilled web designer to create a modern, bold, and engaging WordPress website for Brisolux Consulting Group, LLC. Our company specializes in federal IT consulting, and our name is a play on "Brightening Solutions." The website should reflect our expertise in the federal technology marketplace and position us as a trusted partner for clients navigating their IT journey.

contact: info@brisoluxgrp-example.com

Current Status

WordPress is already installed on our hosting account
We have an existing logo (may need modernization)

Design Requirements

Style:

Modern and visually striking design
Bold elements to convey confidence and expertise
Incorporate the concept of "brightening solutions" into the design

Features:

Modern UX sliders for dynamic content presentation
Eye-catching, high-quality images (stock photos to be sourced by the designer)
Responsive design for all devices

Color Scheme:

To be proposed by the designer, should align with our brand and convey trust and technological expertise

Logo:

Evaluate our current logo
Create a transparent background version if needed
Propose modernization if deemed necessary

Accessibility:

Ensure design elements are accessible to users with disabilities
Use high contrast ratios for text and background colors
Provide text alternatives for non-text content

Website Structure
Create the following pages, with the possibility of subpages:

Home
Services
About
Contact

Specific Page Requirements
Home Page

Striking hero section with a clear value proposition
Overview of our services
Client testimonials or trust indicators

Services Page

Detailed list of our IT consulting services
Clear explanation of how we help navigate the federal IT landscape

About Page

Company history and mission
Team highlights (if applicable)
Our approach to federal IT consulting

Contact Page

Contact form
Other contact methods (phone, email)

Technical Requirements

Fully responsive design
SEO best practices implemented
Fast loading times
Integration with necessary plugins (to be discussed)
Training on how to update and maintain the site
Full compliance with Web Content Accessibility Guidelines (WCAG) 2.1 Level AA
Adherence to Section 508 standards for federal website accessibility
Implementation of necessary features for ADA compliance
Updates

Designs look the same

Target Market(s)

US Federal Govt customers looking for IT support.

Industry/Entity Type

IT Consulting

Coding

Coded - Design and coding required

Colors
0054AA
0677BA
7BADD7
CADEEF
E8F1F8
0094D4
00A9DD
6FCCEA
C7EBF8
E9F6FB
00AB8E
00BBA5
67D7C9
C6EFE9
E9F9F6

```html
<!DOCTYPE html>
<html lang="en">
<head>
<meta charset="utf-8">
<title>Brisolux Consulting Group – Federal IT Consulting</title>
<link href="https://fonts.googleapis.com/css2?family=Outfit:wght@400;500;600;700&display=swap" rel="stylesheet">
<style>
:root{
  --blue-deep:#0054AA;
  --blue-mid:#0677BA;
  --cyan:#00A9DD;
  --cyan-strong:#0094D4;
  --sky:#E9F6FB;
  --navy:#0B2A55;
  --navy-2:#1B3A66;
  --ink:#111827;
  --muted:#4B5563;
  --white:#ffffff;
}
*{box-sizing:border-box;margin:0;padding:0}
html,body{width:1200px;height:4155px;overflow:hidden}
body{font-family:'Outfit',sans-serif;color:var(--ink);background:var(--white);position:relative}
.abs{position:absolute}
.hero-band{left:0;top:0;width:1200px;height:557px;background:linear-gradient(180deg,#E4F4FC,#E9F6FB)}
.brand{left:142px;top:20px;display:flex;align-items:center;gap:10px;font-weight:700;font-size:30px;color:var(--blue-deep);letter-spacing:1px}
.brand .dot{width:28px;height:28px;border-radius:50%;background:var(--cyan)}
.nav-link{top:27px;font-size:13px;font-weight:500;color:var(--ink);text-decoration:none;white-space:nowrap}
.nav-link.active{color:var(--cyan)}
.btn{display:inline-flex;align-items:center;justify-content:center;gap:6px;border-radius:24px;font-weight:600;font-size:13px;text-decoration:none;white-space:nowrap}
.btn-solid{background:var(--blue-deep);color:#fff;box-shadow:0 6px 14px rgba(0,84,170,.3)}
.btn-cyan{background:var(--cyan-strong);color:#fff;box-shadow:0 4px 10px rgba(0,148,212,.35)}
.btn-outline{border:1.5px solid var(--blue-deep);color:var(--blue-deep);background:transparent}
.btn-white{background:#fff;color:var(--blue-deep)}
.eyebrow{font-size:12px;font-weight:600;letter-spacing:.5px;border-left:2px solid var(--blue-deep);padding-left:8px;line-height:15px;text-transform:uppercase}
.eyebrow.blue{color:var(--blue-deep)}
.eyebrow.light{color:#fff;border-color:#fff}
h1,h2{font-weight:600;color:var(--ink)}
.hl{color:var(--cyan)}
.hero-title{left:142px;top:158px;font-size:37px;line-height:46px}
.hero-sub{left:644px;top:196px;font-size:14px;color:var(--ink)}
.photo{border-radius:26px}
.hero-photo{left:142px;top:345px;width:916px;height:387px;background:linear-gradient(180deg,#6f8fb0 0%,#c9c3b4 45%,#9a9a8e 62%,#3f6a2a 80%,#2f5a20 100%)}
.sec-title{font-size:28px;line-height:36px}
.about-text{left:142px;top:946px;width:420px;font-size:11.5px;line-height:22.6px;color:var(--ink)}
.about-text p+p{margin-top:13px}
.about-visual{left:662px;top:826px;width:386px;height:386px;border-radius:50%;background:radial-gradient(circle at 50% 55%,#f1ece2 0%,#cfcac0 55%,#8b8f96 100%)}
.svc-photo{left:0;top:1450px;width:421px;height:342px;border-radius:0 18px 18px 0;background:linear-gradient(180deg,#3d5f93 0%,#d99c5a 45%,#d8d0bd 60%,#4d6b2d 100%)}
.round{border-radius:50%;display:flex;align-items:center;justify-content:center}
.card{background:#fff;border-radius:14px;box-shadow:0 6px 24px rgba(11,42,85,.12);width:213px;height:216px;top:1513px}
.card .icon{position:absolute;left:21px;top:23px;width:55px;height:55px;border-radius:10px;background:var(--blue-deep);display:flex;align-items:center;justify-content:center}
.card h3{position:absolute;left:21px;top:101px;font-size:15.5px;font-weight:500}
.card p{position:absolute;left:21px;top:132px;width:170px;font-size:11px;line-height:19.5px}
.card .go{position:absolute;right:11px;bottom:11px;width:26px;height:26px;background:var(--cyan-strong)}
.testi-band{left:0;top:1877px;width:1200px;height:520px;background:var(--navy)}
.testi-photo{left:600px;top:1994px;width:371px;height:256px;border-radius:14px;background:linear-gradient(180deg,#e7c06b 0%,#c6b48d 40%,#bfbcb2 65%,#8f8a80 100%)}
.testi-box{left:868px;top:2173px;width:190px;height:166px;border-radius:14px;background:var(--navy-2)}
.testi-card{left:258px;top:2113px;width:371px;height:223px;border-radius:12px;background:#fff;box-shadow:0 10px 30px rgba(0,0,0,.25)}
.avatar{position:absolute;left:21px;top:21px;width:56px;height:56px;border-radius:50%;background:linear-gradient(180deg,#d9d3cc,#9b2b33)}
.stars{position:absolute;right:20px;top:28px;display:flex;gap:3px}
.testi-card .name{position:absolute;left:21px;top:88px;font-size:13px;font-weight:600}
.testi-card .role{position:absolute;left:21px;top:111px;font-size:10.5px;color:var(--muted)}
.testi-card .quote{position:absolute;left:21px;top:136px;width:335px;font-size:10.5px;line-height:21px;color:#333}
.center{left:0;width:1200px;text-align:center}
.member{width:184px;text-align:center;top:2595px}
.member .pic{width:184px;height:184px;border-radius:50%;background:linear-gradient(180deg,#dfe7ee 0%,#c2cdd6 55%,#1d2a3a 100%)}
.member .nm{margin-top:28px;font-size:15px;font-weight:600}
.member .rl{margin-top:3px;font-size:11px;color:var(--cyan)}
.member .soc{margin-top:10px;display:flex;gap:10px;justify-content:center}
.member .soc span{width:32px;height:32px;border-radius:50%;background:var(--cyan-strong)}
.cta{left:142px;top:3000px;width:916px;height:328px;border-radius:64px;background:linear-gradient(90deg,#0054AA,#0a60c0)}
.cta-photo{left:629px;top:2944px;width:429px;height:384px;border-radius:0 0 64px 0;background:linear-gradient(180deg,rgba(255,255,255,0) 0%,#e9eef4 30%,#b6c1cf 70%,#4a5c78 100%);clip-path:polygon(55% 0,60% 0,66% 18%,100% 30%,100% 100%,0 100%,0 80%,25% 60%,40% 30%)}
.cta h2{position:absolute;left:55px;top:50px;color:#fff;font-size:27px;line-height:44px;font-weight:500}
.cta p{position:absolute;left:55px;top:152px;width:430px;color:#fff;font-size:13px;line-height:24px}
.cert{top:3557px;height:180px}
.cert-nav{width:34px;height:34px;top:3630px}
.footer{left:0;top:3823px;width:1200px;height:332px;background:linear-gradient(180deg,#12305c,#0B2A55)}
.foot-head{font-size:14px;font-weight:500;color:var(--cyan);top:3895px}
.footer-links{position:absolute;font-size:12px;color:#fff;line-height:27.5px;top:3927px;list-style:none}
.f-contact{position:absolute;left:852px;font-size:12px;color:#fff;display:flex;gap:10px}
.f-contact svg{flex:none}
.social{top:4110px;width:26px;height:26px;border-radius:50%;background:var(--cyan-strong)}
</style>
</head>
<body>

<!-- Hero -->
<div class="abs hero-band"></div>
<div class="abs brand"><span class="dot"></span>BRISOLUX</div>
<a class="abs nav-link active" style="left:695px">Home</a>
<a class="abs nav-link" style="left:770px">About Us</a>
<a class="abs nav-link" style="left:863px">Services</a>
<a class="abs btn btn-cyan" style="left:950px;top:15px;width:108px;height:41px">Contact Us</a>

<div class="abs eyebrow" style="left:142px;top:128px;color:var(--ink);border-color:var(--ink)">Welcome to Brisolux</div>
<h1 class="abs hero-title">Navigate Your Federal<br>IT Journey with<br><span class="hl" style="color:var(--cyan-strong)">Confidence</span>.</h1>
<p class="abs hero-sub">Expert Consulting Services to Guide Your IT Strategy.</p>
<a class="abs btn btn-solid" style="left:644px;top:253px;width:190px;height:41px">Explore Our Services
  <svg width="11" height="11" viewBox="0 0 10 10"><path d="M2 8L8 2M3 2h5v5" stroke="#fff" stroke-width="1.3" fill="none"/></svg></a>
<a class="abs btn btn-outline" style="left:850px;top:253px;width:208px;height:41px">Get A Free Consultation
  <svg width="11" height="11" viewBox="0 0 10 10"><path d="M2 8L8 2M3 2h5v5" stroke="#0054AA" stroke-width="1.3" fill="none"/></svg></a>
<div class="abs photo hero-photo" role="img" aria-label="Photograph of the US Capitol building at sunrise with green lawn in front"></div>

<!-- About -->
<div class="abs eyebrow blue" style="left:142px;top:859px">About Us</div>
<h2 class="abs sec-title" style="left:142px;top:886px">Why Choose <span class="hl">Brisolux?</span></h2>
<div class="abs about-text">
  <p>There are many variations of passages of Lorem Ipsum available, but the majority have suffered alteration in some form, by injected humour, or randomised words which don't look even slightly believable. If you are going to use a passage of Lorem Ipsum, you need to be sure there isn't anything embarrassing hidden in the middle of text.</p>
  <p>It is a long established fact that a reader will be distracted by the readable content of a page when looking at its layout.</p>
</div>
<a class="abs btn btn-solid" style="left:142px;top:1144px;width:129px;height:42px">Learn More
  <svg width="11" height="11" viewBox="0 0 10 10"><path d="M2 8L8 2M3 2h5v5" stroke="#fff" stroke-width="1.3" fill="none"/></svg></a>
<div class="abs about-visual" role="img" aria-label="Photograph of the Capitol dome framed in a circular cut-out"></div>

<!-- Services -->
<div class="abs eyebrow blue" style="left:142px;top:1311px">Popular Services</div>
<h2 class="abs sec-title" style="left:142px;top:1338px">The Best Solution For<br>Your <span class="hl">Business</span></h2>
<div class="abs svc-photo" role="img" aria-label="Photograph of the Capitol building under a sunset sky"></div>
<div class="abs round" style="left:957px;top:1444px;width:38px;height:38px;border:1.5px solid var(--cyan-strong)">
  <svg width="16" height="10" viewBox="0 0 16 10"><path d="M15 5H2M6 1L2 5l4 4" stroke="#0094D4" stroke-width="1.6" fill="none"/></svg></div>
<div class="abs round" style="left:1020px;top:1444px;width:38px;height:38px;background:var(--cyan-strong)">
  <svg width="16" height="10" viewBox="0 0 16 10"><path d="M1 5h13M10 1l4 4-4 4" stroke="#fff" stroke-width="1.6" fill="none"/></svg></div>

<div class="abs card" style="left:377px">
  <div class="icon"><svg width="30" height="30" viewBox="0 0 30 30" fill="none" stroke="#fff" stroke-width="1.6"><path d="M15 5l8 3v6c0 5-3.5 8-8 10-4.5-2-8-5-8-10V8z"/><rect x="11.5" y="13" width="7" height="6" rx="1"/><path d="M13 13v-2a2 2 0 014 0v2"/></svg></div>
  <h3>Cybersecurity</h3><p>There are many variations of passages of Lorem Ipsum available.</p>
  <div class="go round"><svg width="10" height="10" viewBox="0 0 10 10"><path d="M2 8L8 2M3 2h5v5" stroke="#fff" stroke-width="1.4" fill="none"/></svg></div>
</div>
<div class="abs card" style="left:611px">
  <div class="icon"><svg width="30" height="30" viewBox="0 0 30 30" fill="none" stroke="#fff" stroke-width="1.6"><path d="M9 20a5 5 0 010-10 7 7 0 0113 1 4.5 4.5 0 010 9z"/><path d="M12 24h6M15 20v4"/></svg></div>
  <h3>Cloud Services</h3><p>There are many variations of passages of Lorem Ipsum available.</p>
  <div class="go round"><svg width="10" height="10" viewBox="0 0 10 10"><path d="M2 8L8 2M3 2h5v5" stroke="#fff" stroke-width="1.4" fill="none"/></svg></div>
</div>
<div class="abs card" style="left:845px">
  <div class="icon"><svg width="30" height="30" viewBox="0 0 30 30" fill="none" stroke="#fff" stroke-width="1.6"><rect x="6" y="17" width="18" height="8" rx="1"/><circle cx="15" cy="9" r="3"/><path d="M10 17a5 5 0 0110 0"/></svg></div>
  <h3>IT Strategy Consulting</h3><p>There are many variations of passages of Lorem Ipsum available.</p>
  <div class="go round"><svg width="10" height="10" viewBox="0 0 10 10"><path d="M2 8L8 2M3 2h5v5" stroke="#fff" stroke-width="1.4" fill="none"/></svg></div>
</div>

<!-- Testimonials -->
<div class="abs testi-band"></div>
<div class="abs eyebrow light" style="left:142px;top:1995px">Our Testimonials</div>
<h2 class="abs sec-title" style="left:142px;top:2022px;color:#fff">Hear What Our <span class="hl">Clients Say</span></h2>
<div class="abs testi-box"></div>
<div class="abs testi-photo" role="img" aria-label="Photograph of the Capitol dome seen through autumn trees"></div>
<div class="abs testi-card">
  <div class="avatar" role="img" aria-label="Client portrait"></div>
  <div class="stars">
    <svg width="14" height="14" viewBox="0 0 10 10"><path d="M5 .5l1.3 3 3.2.3-2.4 2.1.7 3.2L5 7.5 2.2 9.1l.7-3.2L.5 3.8l3.2-.3z" fill="#F5A524"/></svg>
    <svg width="14" height="14" viewBox="0 0 10 10"><path d="M5 .5l1.3 3 3.2.3-2.4 2.1.7 3.2L5 7.5 2.2 9.1l.7-3.2L.5 3.8l3.2-.3z" fill="#F5A524"/></svg>
    <svg width="14" height="14" viewBox="0 0 10 10"><path d="M5 .5l1.3 3 3.2.3-2.4 2.1.7 3.2L5 7.5 2.2 9.1l.7-3.2L.5 3.8l3.2-.3z" fill="#F5A524"/></svg>
    <svg width="14" height="14" viewBox="0 0 10 10"><path d="M5 .5l1.3 3 3.2.3-2.4 2.1.7 3.2L5 7.5 2.2 9.1l.7-3.2L.5 3.8l3.2-.3z" fill="#F5A524"/></svg>
    <svg width="14" height="14" viewBox="0 0 10 10"><path d="M5 .5l1.3 3 3.2.3-2.4 2.1.7 3.2L5 7.5 2.2 9.1l.7-3.2L.5 3.8l3.2-.3z" fill="#F5A524"/></svg>
  </div>
  <div class="name">Marcus T. Ellingwood</div>
  <div class="role">CEO &amp; Founder</div>
  <p class="quote">It is a long established fact that a reader will be distracted by the readable content of a page when looking at its layout. The point of using Lorem Ipsum is that it has a more-or-less normal distribution.</p>
</div>
<div class="abs round" style="left:945px;top:2284px;width:36px;height:36px;border:1.5px solid #fff">
  <svg width="14" height="10" viewBox="0 0 16 10"><path d="M15 5H2M6 1L2 5l4 4" stroke="#fff" stroke-width="1.6" fill="none"/></svg></div>
<div class="abs round" style="left:1001px;top:2284px;width:36px;height:36px;background:#fff">
  <svg width="14" height="10" viewBox="0 0 16 10"><path d="M1 5h13M10 1l4 4-4 4" stroke="#0B2A55" stroke-width="1.6" fill="none"/></svg></div>

<!-- Team -->
<div class="abs center" style="top:2483px"><span class="eyebrow blue">Our Team</span></div>
<h2 class="abs center sec-title" style="top:2510px">Meet The Our <span class="hl">Experts</span></h2>
<div class="abs member" style="left:174px"><div class="pic" role="img" aria-label="Team member portrait"></div><div class="nm">Clara Wendt</div><div class="rl">Web Designer</div><div class="soc"><span aria-label="Professional network profile"></span><span aria-label="Social profile"></span></div></div>
<div class="abs member" style="left:397px"><div class="pic" role="img" aria-label="Team member portrait"></div><div class="nm">Owen Tarrick</div><div class="rl">Web Designer</div><div class="soc"><span aria-label="Professional network profile"></span><span aria-label="Social profile"></span></div></div>
<div class="abs member" style="left:619px"><div class="pic" role="img" aria-label="Team member portrait"></div><div class="nm">Lena Morvay</div><div class="rl">Web Designer</div><div class="soc"><span aria-label="Professional network profile"></span><span aria-label="Social profile"></span></div></div>
<div class="abs member" style="left:840px"><div class="pic" role="img" aria-label="Team member portrait"></div><div class="nm">Julian Averett</div><div class="rl">Web Designer</div><div class="soc"><span aria-label="Professional network profile"></span><span aria-label="Social profile"></span></div></div>

<!-- Call to action -->
<div class="abs cta">
  <h2>We Are Federal IT Consulting<br>We Make Future!</h2>
  <p>There are many variations of passages of Lorem Ipsum available, but the majority have suffered alteration in some form.</p>
  <a class="abs btn btn-white" style="left:55px;top:236px;width:163px;height:42px">Get Started Now
    <svg width="11" height="11" viewBox="0 0 10 10"><path d="M2 8L8 2M3 2h5v5" stroke="#0054AA" stroke-width="1.3" fill="none"/></svg></a>
</div>
<div class="abs cta-photo" role="img" aria-label="Photograph of the Capitol dome with flag rising above the banner"></div>

<!-- Certifications -->
<div class="abs center" style="top:3417px"><span class="eyebrow blue">Certifications</span></div>
<h2 class="abs center sec-title" style="top:3444px">Certificates Of The Most<br>Popular <span class="hl">Brands</span></h2>
<div class="abs round cert-nav" style="left:141px;border:1.5px solid var(--blue-deep)">
  <svg width="8" height="12" viewBox="0 0 8 12"><path d="M6 1L1 6l5 5" stroke="#0054AA" stroke-width="1.6" fill="none"/></svg></div>
<div class="abs cert" role="img" aria-label="Certificate of achievement" style="left:197px;width:253px;background:#f6eee2"></div>
<div class="abs cert" role="img" aria-label="Certificate of recognition" style="left:481px;width:240px;top:3563px;height:170px;background:#e6e8ec"></div>
<div class="abs cert" role="img" aria-label="Certificate of achievement" style="left:752px;width:251px;background:linear-gradient(90deg,#c9d0dc,#f2f3f5)"></div>
<div class="abs round cert-nav" style="left:1023px;background:var(--blue-deep)">
  <svg width="8" height="12" viewBox="0 0 8 12"><path d="M2 1l5 5-5 5" stroke="#fff" stroke-width="1.6" fill="none"/></svg></div>

<!-- Footer -->
<footer class="abs footer" role="img" aria-label="Footer background with a faint Capitol photograph"></footer>
<div class="abs brand" style="left:142px;top:3915px;color:#fff;font-size:38px"><span class="dot" style="width:34px;height:34px"></span>BRISOLUX</div>
<h4 class="abs foot-head" style="left:511px">Quick Links</h4>
<ul class="footer-links" style="left:511px"><li>Home</li><li>About Us</li><li>Services</li></ul>
<h4 class="abs foot-head" style="left:673px">Resources</h4>
<ul class="footer-links" style="left:673px"><li>Privacy Policy</li><li>Terms Of Service</li></ul>
<h4 class="abs foot-head" style="left:852px">Contact Info</h4>
<div class="f-contact" style="top:3930px">
  <svg width="14" height="18" viewBox="0 0 14 18"><path d="M7 1a6 6 0 016 6c0 4.5-6 10-6 10S1 11.5 1 7a6 6 0 016-6z" fill="#00A9DD"/><circle cx="7" cy="7" r="2.2" fill="#0B2A55"/></svg>
  <span style="line-height:16px">48 Harbor Lane, Suite 210<br>Fairview Road 5521</span></div>
<div class="f-contact" style="top:3981px">
  <svg width="16" height="12" viewBox="0 0 16 12"><rect x="0.5" y="0.5" width="15" height="11" rx="1.5" fill="#00A9DD"/><path d="M1 1.5l7 5 7-5" stroke="#0B2A55" stroke-width="1.2" fill="none"/></svg>
  <span>info@brisoluxgrp-example.com</span></div>
<div class="f-contact" style="top:4015px">
  <svg width="15" height="15" viewBox="0 0 15 15"><path d="M3 1l3 3-1.5 2a8 8 0 004.5 4.5L11 9l3 3-2 2C6 14 1 9 1 3z" fill="#00A9DD"/></svg>
  <span>555-014-2236</span></div>
<div class="abs" style="left:142px;top:4094px;width:916px;height:1px;background:rgba(255,255,255,.25)"></div>
<div class="abs" style="left:142px;top:4116px;font-size:11.5px;color:#fff">© 2024 Brisolux. All rights reserved.</div>
<div class="abs social" style="left:910px" aria-label="Photo sharing profile"></div>
<div class="abs social" style="left:950px" aria-label="Microblog profile"></div>
<div class="abs social" style="left:990px" aria-label="Social profile"></div>
<div class="abs social" style="left:1031px" aria-label="Professional network profile"></div>

</body>
</html>
```